Veranix - Solution provider in business consulting

Veranix is a swiss based company providing solutions for developing markets. The business covers various fields of business consulting, such as supply chain, product costs, quality management and manufacturing management. The Business operates in a efficient, straight and solution oriented manner.
The final design should communicate these characteristics. Asian people as well as as western people shall identify the qualities of the company at first sight.
The customer needs business cards with a simple view but an recognizable design, printed in high quality. Engraved elements such as the globe or simple words are possible.
Available colors are: (RAL)
102/102/102
51/102/102
153/204/153
255/102/51
Font: Calibri

```html
<!DOCTYPE html>
<html lang="en">
<head>
<meta charset="utf-8">
<title>Veranix Business Card</title>
<link rel="stylesheet" href="https://fonts.googleapis.com/css2?family=Carlito:wght@400;700&display=swap">
<style>
  :root {
    --backdrop-top: #2b2b2b;
    --backdrop-bottom: #050505;
    --card-white: #ffffff;
    --brand-grey: #666666;
    --text-dark: #222222;
    --text-mid: #444444;
    --back-grey: #666666;
    --emboss-light: #727272;
    --emboss-dark: #5e5e5e;
  }
  * { box-sizing: border-box; margin: 0; padding: 0; }
  html, body {
    width: 1200px;
    height: 900px;
    overflow: hidden;
  }
  body {
    position: relative;
    background: linear-gradient(180deg, var(--backdrop-top) 0%, #1a1a1a 55%, var(--backdrop-bottom) 100%);
    font-family: "Carlito", "Calibri", sans-serif;
  }
  .card {
    position: absolute;
    top: 170px;
    width: 347px;
    height: 561px;
    overflow: hidden;
  }
  .card-front {
    left: 259px;
    background: var(--card-white);
    color: var(--text-mid);
    text-align: center;
  }
  .card-back {
    left: 631px;
    background: var(--back-grey);
  }
  .emboss-area {
    position: absolute;
    left: 10px;
    top: 112px;
    width: 330px;
    height: 330px;
    border-radius: 50%;
    background: radial-gradient(circle at 60% 40%, var(--emboss-light) 0%, var(--back-grey) 60%, var(--emboss-dark) 100%);
  }
  .edge-tab {
    position: absolute;
    left: 102px;
    width: 143px;
    background: var(--brand-grey);
  }
  .edge-tab-top { top: 0; height: 30px; }
  .edge-tab-bottom { bottom: 0; height: 28px; }
  .brand-name {
    position: absolute;
    top: 126px;
    left: 0;
    width: 100%;
    font-size: 52px;
    font-weight: 400;
    letter-spacing: 1px;
    color: var(--brand-grey);
    line-height: 1;
  }
  .person-name {
    position: absolute;
    top: 262px;
    width: 100%;
    font-size: 21px;
    font-weight: 700;
    color: var(--text-dark);
  }
  .person-role {
    position: absolute;
    top: 288px;
    width: 100%;
    font-size: 15px;
    color: var(--text-mid);
  }
  .contact-list {
    position: absolute;
    top: 323px;
    width: 100%;
    list-style: none;
    font-size: 16px;
    line-height: 23px;
  }
  .contact-list li {
    display: flex;
    justify-content: center;
    align-items: center;
    gap: 9px;
  }
  .contact-icon {
    width: 12px;
    height: 12px;
    fill: var(--text-mid);
  }
  .company-address {
    position: absolute;
    top: 421px;
    width: 100%;
    font-size: 16px;
    line-height: 21px;
    font-style: normal;
  }
</style>
</head>
<body>
  <section class="card card-front" aria-label="Front of business card">
    <div class="edge-tab edge-tab-top"></div>
    <div class="brand-name">veranix</div>
    <h1 class="person-name">Lukas Brenner</h1>
    <p class="person-role">CEO</p>
    <ul class="contact-list">
      <li>
        <svg class="contact-icon" viewBox="0 0 12 12" aria-hidden="true"><path d="M3 0h6a1 1 0 0 1 1 1v10a1 1 0 0 1-1 1H3a1 1 0 0 1-1-1V1a1 1 0 0 1 1-1zm0.6 1.4v7.8h4.8V1.4zM6 9.8a0.7 0.7 0 1 0 0 1.4a0.7 0.7 0 1 0 0-1.4z"/></svg>
        <span>+41 79 555 0182</span>
      </li>
      <li>
        <svg class="contact-icon" viewBox="0 0 12 12" aria-hidden="true"><path d="M2.4 0.4l1.8 0l1 2.8l-1.3 1a7 7 0 0 0 3.9 3.9l1-1.3l2.8 1l0 1.8a1.2 1.2 0 0 1-1.3 1.2A10.5 10.5 0 0 1 0.4 1.7A1.2 1.2 0 0 1 1.6 0.4z"/></svg>
        <span>+41 71 555 0347</span>
      </li>
      <li>
        <svg class="contact-icon" viewBox="0 0 12 12" aria-hidden="true"><path d="M0 2h12v8H0zM1 3v0.4l5 3.2l5-3.2V3zM1 4.6V9h10V4.6L6 7.8z"/></svg>
        <span>lukas.brenner@veranix.ch</span>
      </li>
      <li>
        <svg class="contact-icon" viewBox="0 0 12 12" aria-hidden="true"><circle cx="6" cy="6" r="6"/></svg>
        <span>www.veranix.ch</span>
      </li>
    </ul>
    <address class="company-address">
      Veranix GmbH Lindenweg 14<br>
      9215 Felsberg Switzerland
    </address>
    <div class="edge-tab edge-tab-bottom"></div>
  </section>

  <section class="card card-back" aria-label="Back of business card">
    <div class="emboss-area" role="img" aria-label="Blind-embossed globe decoration showing the brand symbol"></div>
  </section>
</body>
</html>
```